CM Candle Tube Packaging Design

Website: www.corvelmare.example
IG: @corvel.mare
Tagline: Elevate Your Ambiance
My brand is a sophisticated brand with luxury candles made of coconut wax. Im looking for an upscale minimalist chic design.
Discover the transformative power of positive energy with Corvel Mare candles. Indulge in true luxury with our specially crafted coconut wax blend that not only ignites captivating scents but also embodies modern elegance and empowering elements.
At Corvel Mare we're committed to delivering a unique and exhilarating aromatic experience to all candle lovers. Each candle is meticulously handcrafted in small batches using luxury fragrance oils exclusively formulated for coconut wax.
Our candles are:
Clean-burning
Paraben-Free
Phthalate-Free
Skin-Safe
Pet-Friendly

```html
<!DOCTYPE html>
<html lang="en">
<head>
<meta charset="utf-8">
<title>Corvel Mare — Candle Label</title>
<link rel="stylesheet" href="https://fonts.googleapis.com/css2?family=Italiana&family=Great+Vibes&family=Poppins:wght@300;400&display=swap">
<style>
  :root {
    --backdrop: #434f44;
    --label-white: #ffffff;
    --ink: #2c2626;
    --cocoa: #6a3a36;
    --rose: #e0a89e;
    --gold: #d4ab4a;
    --gold-light: #f1d98e;
    --rule: #7b5a55;
  }
  * { margin: 0; padding: 0; box-sizing: border-box; }
  html, body { width: 1200px; height: 2824px; overflow: hidden; }
  body {
    background: var(--backdrop);
    position: relative;
    font-family: "Poppins", sans-serif;
  }
  .label {
    position: absolute;
    left: 100px; top: 600px;
    width: 1000px; height: 1624px;
    background: var(--label-white);
    box-shadow: 0 10px 40px rgba(0,0,0,0.35);
    overflow: hidden;
  }
  .brand-name {
    position: absolute; left: 0; right: 0; top: 318px;
    text-align: center;
    font-family: "Italiana", serif;
    font-size: 92px; line-height: 1;
    color: var(--ink);
    letter-spacing: -1px;
  }
  .brand-descriptor {
    position: absolute; left: 0; right: 0; top: 438px;
    display: flex; justify-content: center; align-items: center; gap: 20px;
    font-family: "Poppins", sans-serif; font-weight: 400;
    font-size: 21px; letter-spacing: 10px;
    color: var(--ink);
  }
  .brand-descriptor::before, .brand-descriptor::after {
    content: ""; width: 36px; height: 2px; background: var(--ink);
  }
  .brand-motto {
    position: absolute; left: 0; right: 0; top: 476px;
    text-align: center;
    font-family: "Great Vibes", cursive;
    font-size: 26px; color: var(--cocoa);
  }
  .floral { position: absolute; }
  .floral-right {
    left: 849px; top: 560px; width: 151px; height: 452px;
    background: radial-gradient(ellipse at 40% 50%, rgba(212,171,74,0.45), rgba(241,217,142,0.15) 60%, rgba(255,255,255,0) 80%);
  }
  .floral-left {
    left: 0; top: 1018px; width: 149px; height: 458px;
    background: radial-gradient(ellipse at 60% 55%, rgba(212,171,74,0.45), rgba(241,217,142,0.15) 60%, rgba(255,255,255,0) 80%);
  }
  .feature-panel {
    position: absolute;
    left: 149px; top: 533px; width: 700px; height: 968px;
    border: 4px solid var(--gold);
    border-image: linear-gradient(135deg, var(--gold), var(--gold-light), var(--gold)) 1;
    background: var(--label-white);
    box-shadow: 0 18px 22px -12px rgba(212,171,74,0.45);
  }
  .tagline {
    position: absolute; left: 0; right: 0; top: 70px;
    text-align: center;
    font-family: "Great Vibes", cursive;
    font-size: 128px; line-height: 118px;
    color: var(--cocoa);
  }
  .tagline-rule {
    position: absolute; left: 39px; right: 26px; top: 344px;
    height: 2px; background: var(--rule);
  }
  .benefits {
    position: absolute; left: 0; right: 0; top: 384px;
    list-style: none; text-align: center;
    font-size: 44px; line-height: 62px; font-weight: 400;
    color: var(--ink);
  }
  .flame-icon {
    position: absolute; left: 320px; top: 712px;
  }
  .product-spec {
    position: absolute; left: 0; right: 0; top: 826px;
    text-align: center;
    font-size: 32px; line-height: 50px;
    color: var(--cocoa);
  }
</style>
</head>
<body>
  <main class="label">
    <div class="brand-name">CORVEL MARE</div>
    <div class="brand-descriptor">HANDMADE CANDLES</div>
    <div class="brand-motto">with purpose and love</div>

    <div class="floral floral-right" role="img" aria-label="Gold line-art wildflowers and leafy stems"></div>
    <div class="floral floral-left" role="img" aria-label="Gold line-art wildflowers and wheat stems"></div>

    <section class="feature-panel">
      <h1 class="tagline">Elevate Your<br>Ambiance</h1>
      <div class="tagline-rule"></div>
      <ul class="benefits">
        <li>Clean-burning</li>
        <li>Paraben-Free</li>
        <li>Phthalate-Free</li>
        <li>Skin-Safe</li>
        <li>Pet-Friendly</li>
      </ul>
      <svg class="flame-icon" width="56" height="100" viewBox="0 0 56 100" aria-hidden="true">
        <path d="M28 2 C36 26 54 44 52 70 C50 88 40 98 28 98 C16 98 6 88 4 70 C2 48 22 34 28 2 Z" fill="var(--rose)"/>
      </svg>
      <p class="product-spec">COCONUT WAX CANDLE<br>14OZ. (396G)</p>
    </section>
  </main>
</body>
</html>
```